BrivoTerna. Lantern of the Steady Harvest. Business card

Professional business card for BrivoTerna (Lantern of the Steady Harvest)
My rationale: Strategy-> Execution-> Results-> Value that lead to the BrivoTerna name: We put the Lantern of the Steady Harvest.
We deliver value to our customers helping them at defining a good strategy (cyan arrow). 90% of well formulated strategies fail due to poor execution so we also consider strategical execution very important (green arrow). Due to the execution we obtain the results (blue arrow). Finally, the results provide feedback to redefine strategy, and the new strategy has to be executed and new results obtained providing new feedback and on and on. It's like a wheel that finally, must create corporate value: value for shareholders, staholders, employees, providers...-

Target Market(s)

CEOs and steering comitees , invewrnent funds

Industry/Entity Type

Business Consultant

Contact Information for Business Card

Teodoro Vinsquel
CEO & Founder
teodoro.vinsquel@brivoterna-example.com
Mobile: +34 655.803.912
www.brivoterna-example.com

Colors

Designer to choose colors to be used in the design.

Requirements
Nice to have
• Nice to hace the words: Strategy, execution, results
• Nice to vave the claim: Lantern of the Steady Harvest
• The three colors should be shown:
• cyan for STRATEGY
• green for EXECUTION
• blue for RESULTS
Should not have
• Complete black background

```html
<!DOCTYPE html>
<html lang="en">
<head>
<meta charset="utf-8">
<title>BrivoTerna – Business Card</title>
<link rel="stylesheet" href="https://fonts.googleapis.com/css2?family=Roboto:wght@300;400;500;700&display=swap">
<style>
  :root {
    --backdrop: #333437;
    --card: #1f2022;
    --card-back: #1d1e20;
    --pattern-tone: #2b2c2f;
    --white: #ffffff;
    --light: #e6e6e6;
    --muted: #bdbdbd;
    --rule: #8a8a8a;
    --cyan: #1ea7e4;
  }
  html, body {
    margin: 0;
    padding: 0;
    width: 1200px;
    height: 1108px;
    overflow: hidden;
    background: var(--backdrop);
    font-family: "Roboto", Arial, sans-serif;
  }
  .canvas {
    position: relative;
    width: 1200px;
    height: 1108px;
  }
  .card {
    position: absolute;
    top: 244px;
    width: 400px;
    height: 620px;
    border-radius: 22px;
    box-shadow: 0 18px 40px rgba(0,0,0,0.45);
    overflow: hidden;
  }
  .card--front {
    left: 150px;
    background: var(--card);
  }
  .card--back {
    left: 650px;
    background: var(--card-back);
  }

  /* Front */
  .brand-name {
    position: absolute;
    top: 190px;
    left: 0;
    width: 100%;
    text-align: center;
    font-weight: 700;
    font-size: 56px;
    letter-spacing: -1px;
    color: var(--white);
  }
  .person {
    position: absolute;
    top: 372px;
    width: 100%;
    text-align: center;
  }
  .person__name {
    font-weight: 700;
    font-size: 25px;
    color: var(--cyan);
    margin: 0;
  }
  .person__title {
    font-weight: 400;
    font-size: 15px;
    color: var(--light);
    margin: 4px 0 0;
  }
  .divider {
    position: absolute;
    top: 432px;
    left: 30px;
    width: 340px;
    height: 34px;
  }
  .contacts {
    position: absolute;
    top: 484px;
    width: 100%;
    text-align: center;
    font-weight: 300;
    font-size: 16px;
    line-height: 27px;
    color: var(--light);
  }
  .contacts p { margin: 0; }

  /* Back */
  .back-pattern {
    position: absolute;
    inset: 0;
    background: linear-gradient(160deg, var(--pattern-tone) 0%, var(--card-back) 90%);
  }
  .back-mark {
    position: absolute;
    left: 236px;
    top: 452px;
    display: flex;
    align-items: center;
    gap: 8px;
    font-weight: 700;
    font-size: 22px;
    color: var(--cyan);
  }
  .back-mark__dot {
    width: 12px;
    height: 12px;
    border-radius: 50%;
    background: var(--cyan);
  }
</style>
</head>
<body>
<main class="canvas">

  <section class="card card--front" aria-label="Business card front">
    <div class="brand-name">BrivoTerna</div>

    <div class="person">
      <p class="person__name">Teodoro Vinsquel</p>
      <p class="person__title">CEO &amp; Founder</p>
    </div>

    <svg class="divider" viewBox="0 0 340 34" aria-hidden="true">
      <line x1="0" y1="17" x2="120" y2="17" stroke="var(--rule)" stroke-width="1.2"/>
      <line x1="220" y1="17" x2="340" y2="17" stroke="var(--rule)" stroke-width="1.2"/>
      <!-- phone -->
      <circle cx="136" cy="17" r="14" fill="var(--cyan)"/>
      <path d="M129 12 q0-3 3-3 l2 0 1 4 -2 1.5 q1.5 3.5 5 5 l1.5-2 4 1 0 2 q0 3-3 3 q-11-1-11.5-11.5z" fill="var(--card)"/>
      <!-- mail -->
      <circle cx="170" cy="17" r="14" fill="var(--cyan)"/>
      <rect x="161" y="11" width="18" height="12" rx="1.5" fill="var(--card)"/>
      <path d="M161.5 11.5 L170 18 L178.5 11.5" fill="none" stroke="var(--cyan)" stroke-width="1.5"/>
      <!-- globe -->
      <circle cx="204" cy="17" r="14" fill="var(--cyan)"/>
      <circle cx="204" cy="17" r="8.5" fill="none" stroke="var(--card)" stroke-width="2"/>
      <ellipse cx="204" cy="17" rx="3.6" ry="8.5" fill="none" stroke="var(--card)" stroke-width="1.6"/>
      <line x1="195.5" y1="17" x2="212.5" y2="17" stroke="var(--card)" stroke-width="1.6"/>
    </svg>

    <div class="contacts">
      <p>+34 655.803.912</p>
      <p>www.brivoterna-example.com</p>
      <p>teodoro.vinsquel@brivoterna-example.com</p>
    </div>
  </section>

  <section class="card card--back" aria-label="Business card back">
    <div class="back-pattern" role="img" aria-label="Faint repeating brand pattern in dark grey tones"></div>
    <div class="back-mark">
      <span class="back-mark__dot"></span>
      <span>BrivoTerna</span>
    </div>
  </section>

</main>
</body>
</html>
```